Flyer für unser Jubiläumscamp "herbstcamp"

Am 10. - 14.10.2022 und 17. - 21. 10.2022 organisieren wir je eine Woche ein Fussballcamp für Kinder ab 5 Jahren bis 12 Jahren. Ebenfalls feiern wir unser 5 jähriges Jubiläum und bieten deshalb das Camp für 300 statt 350 CHF an.
Für dieses Camp (mit dieses 2 Angeboten) möchten wir einen speziellen Flyer haben. Der Flyedr sollte Kinder freundlich aber auch modern sein. Wir bieten auch ein Leistungs, Girls Only sowie ein Goalicamp. (eventuell ist dies aber zu überlastet dan)
Infos zu unseren Camps: https://wolbaspiel.ch/events/2022-sommercamps-juli/

Target Market(s)

Kinder, 5-12 Jahre

Requirements
Must have
• Logo, Fun Kidscamp
Should not have
• Gleiches wie der Flyer angehängt.

```html
<!DOCTYPE html>
<html lang="de">
<head>
<meta charset="UTF-8">
<title>Herbstcamp Flyer</title>
<link href="https://fonts.googleapis.com/css2?family=Montserrat:wght@400;600;700;800&display=swap" rel="stylesheet">
<style>
  :root {
    --navy: #1f3a72;
    --orange: #ef8519;
    --yellow: #ffe100;
    --white: #ffffff;
    --ink: #1d1d1d;
    --footer: #2a2a2c;
    --grass: #5f9a3a;
  }
  * { margin: 0; padding: 0; box-sizing: border-box; }
  html, body { width: 783px; height: 1200px; overflow: hidden; background: var(--white); }
  body { font-family: "Montserrat", sans-serif; }
  .flyer { position: relative; width: 783px; height: 1200px; overflow: hidden; background: var(--white); }

  .hero { position: absolute; left: 0; top: 0; width: 783px; height: 500px; }
  .brand { position: absolute; left: 46px; top: 70px; display: flex; align-items: center; gap: 12px;
    color: var(--white); font-weight: 700; font-size: 28px; }
  .brand-dot { width: 34px; height: 34px; border-radius: 50%; background: var(--orange); }
  .age { position: absolute; left: 44px; top: 206px; color: var(--white); font-weight: 400;
    font-size: 58px; line-height: 58px; letter-spacing: -0.5px; }
  .hero-rule { position: absolute; left: 46px; top: 356px; width: 345px; height: 1px; background: rgba(255,255,255,0.35); }
  .title { position: absolute; left: 42px; top: 372px; color: var(--yellow); font-weight: 800;
    font-size: 64px; letter-spacing: -1px; line-height: 64px; }
  .offer { position: absolute; left: 46px; top: 444px; color: var(--white); font-weight: 700;
    font-size: 19px; line-height: 24px; }
  .offer s { color: rgba(255,255,255,0.6); font-weight: 600; }

  .location { position: absolute; left: 0; top: 500px; width: 783px; height: 146px; background: var(--orange);
    color: var(--white); text-align: center; }
  .location-name { position: absolute; left: 0; right: 0; top: 8px; font-size: 46px; font-weight: 600; letter-spacing: -0.5px; }
  .camp-types { position: absolute; left: 0; right: 0; top: 80px; display: flex; justify-content: center; gap: 24px;
    font-size: 22px; font-weight: 700; list-style: none; }
  .camp-types li { display: flex; align-items: center; gap: 6px; }

  .gallery { position: absolute; top: 674px; left: 47px; display: flex; gap: 32px; }
  .gallery-photo { width: 208px; height: 178px; border-radius: 10px; border: 3px solid var(--white);
    box-shadow: 0 2px 6px rgba(0,0,0,0.3); }
  .photo-goal { background: linear-gradient(180deg, #8fb2d6 0%, #5d8a44 55%, #78a84c 100%); }
  .photo-team { background: linear-gradient(180deg, #9fc0dd 0%, #5e8c3f 50%, #6f9e48 100%); }
  .photo-mascot { background: linear-gradient(90deg, #7ea4c8 0%, #ef7a1c 55%, #2a4fa0 100%); }

  .dates { position: absolute; left: 91px; top: 903px; width: 599px; height: 97px; border: 1.5px solid var(--ink); }
  .dates-icon { position: absolute; top: 26px; width: 44px; height: 44px; border-radius: 50%; background: var(--orange); }
  .dates-icon.left { left: 40px; }
  .dates-icon.right { right: 40px; }
  .date-line { position: absolute; left: 0; right: 0; text-align: center; color: var(--ink); font-weight: 700;
    font-size: 34px; line-height: 40px; }
  .date-line.first { top: -22px; }
  .date-line.first span { background: var(--white); padding: 0 14px; position: relative; }
  .date-line.first span::before, .date-line.first span::after { content: ""; position: absolute; top: 15px;
    width: 9px; height: 9px; border-radius: 50%; background: var(--orange); }
  .date-line.first span::before { left: 0; }
  .date-line.first span::after { right: 0; }
  .date-line.second { top: 28px; }

  .signup { position: absolute; left: 0; right: 0; top: 1022px; text-align: center; color: var(--navy);
    font-weight: 800; font-size: 38px; letter-spacing: -1px; }

  .contact { position: absolute; left: 0; top: 1088px; width: 783px; height: 112px; background: var(--footer);
    color: var(--white); display: flex; justify-content: center; align-items: flex-start; padding-top: 22px;
    gap: 16px; font-weight: 700; font-size: 24px; }
  .contact-item { display: flex; align-items: center; gap: 8px; }
  .contact-sep { width: 2px; height: 28px; background: var(--white); }
</style>
</head>
<body>
<main class="flyer">
  <svg class="hero" viewBox="0 0 783 500" xmlns="http://www.w3.org/2000/svg">
    <rect width="783" height="500" fill="var(--navy)"/>
    <circle cx="338" cy="222" r="88" fill="var(--white)" role="img" aria-label="Fussball-Illustration"/>
    <path d="M455 0 C350 110 345 330 545 500 L783 500 L783 0 Z" fill="var(--yellow)"/>
    <defs>
      <linearGradient id="pitch" x1="0" y1="0" x2="0" y2="1">
        <stop offset="0" stop-color="#a9c3cf"/>
        <stop offset="0.45" stop-color="#6d9a57"/>
        <stop offset="1" stop-color="var(--grass)"/>
      </linearGradient>
    </defs>
    <path d="M488 0 C385 110 382 320 580 500 L783 500 L783 0 Z" fill="url(#pitch)" role="img"
      aria-label="Foto: zwei Kinder spielen Fussball auf dem Rasen"/>
    <path d="M0 486 q8.25 -16 16.5 0 t16.5 0 t16.5 0 t16.5 0 t16.5 0 t16.5 0 t16.5 0 t16.5 0 t16.5 0 t16.5 0 t16.5 0 t16.5 0 t16.5 0 t16.5 0 t16.5 0 t16.5 0 t16.5 0 t16.5 0 t16.5 0 t16.5 0 t16.5 0 t16.5 0 t16.5 0 t16.5 0 t16.5 0 t16.5 0 t16.5 0 t16.5 0 t16.5 0 t16.5 0 t16.5 0 t16.5 0 t16.5 0 t16.5 0 t16.5 0 t16.5 0 t16.5 0 t16.5 0 t16.5 0 t16.5 0 t16.5 0 t16.5 0 t16.5 0 t16.5 0 t16.5 0 t16.5 0 t16.5 0 t16.5 0 L800 510 L0 510 Z"
      fill="var(--orange)" stroke="var(--white)" stroke-width="5"/>
  </svg>

  <div class="brand"><span class="brand-dot"></span>Wolbaspiel</div>
  <p class="age">ab 5<br>Jahren</p>
  <div class="hero-rule"></div>
  <h1 class="title">KIDSCAMPS</h1>
  <p class="offer">5 Jahre Jubiläum: 300 CHF <s>350</s></p>

  <section class="location">
    <h2 class="location-name">HERBSTCAMP ZURICH</h2>
    <ul class="camp-types">
      <li><svg width="18" height="18" viewBox="0 0 18 18"><circle cx="9" cy="9" r="9" fill="var(--white)"/><path d="M5 9.2 L8 12 L13 6.5" fill="none" stroke="var(--orange)" stroke-width="2.4" stroke-linecap="round" stroke-linejoin="round"/></svg>Leistungscamp</li>
      <li><svg width="18" height="18" viewBox="0 0 18 18"><circle cx="9" cy="9" r="9" fill="var(--white)"/><path d="M5 9.2 L8 12 L13 6.5" fill="none" stroke="var(--orange)" stroke-width="2.4" stroke-linecap="round" stroke-linejoin="round"/></svg>Girls Only</li>
      <li><svg width="18" height="18" viewBox="0 0 18 18"><circle cx="9" cy="9" r="9" fill="var(--white)"/><path d="M5 9.2 L8 12 L13 6.5" fill="none" stroke="var(--orange)" stroke-width="2.4" stroke-linecap="round" stroke-linejoin="round"/></svg>Goalicamp</li>
    </ul>
  </section>

  <section class="gallery">
    <div class="gallery-photo photo-goal" role="img" aria-label="Foto: Fussballtor auf dem Trainingsplatz"></div>
    <div class="gallery-photo photo-team" role="img" aria-label="Foto: Kinder mit Trainern und Bällen auf dem Rasen"></div>
    <div class="gallery-photo photo-mascot" role="img" aria-label="Foto: Camp-Maskottchen mit Kindern auf dem Platz"></div>
  </section>

  <section class="dates">
    <span class="dates-icon left"></span>
    <span class="dates-icon right"></span>
    <p class="date-line first"><span>10. - 14.10.2022</span></p>
    <p class="date-line second">17. - 21.10.2022</p>
  </section>

  <h3 class="signup">ANMELDUNG UNTER</h3>

  <footer class="contact">
    <span class="contact-item">
      <svg width="26" height="18" viewBox="0 0 26 18"><rect x="1" y="1" width="24" height="16" fill="var(--orange)"/><path d="M1 1 L13 10 L25 1 M1 17 L10 8 M25 17 L16 8" fill="none" stroke="var(--footer)" stroke-width="1.6"/></svg>
      info@wolbaspiel.ch
    </span>
    <span class="contact-sep"></span>
    <span class="contact-item">
      <svg width="24" height="24" viewBox="0 0 24 24" fill="none" stroke="var(--orange)" stroke-width="2"><circle cx="12" cy="12" r="10"/><ellipse cx="12" cy="12" rx="4.5" ry="10"/><path d="M2 12 H22 M4 6.5 H20 M4 17.5 H20"/></svg>
      www.wolbaspiel.ch
    </span>
  </footer>
</main>
</body>
</html>
```